Bright, Bold Sydney Tutoring Business Flyer Advertisment

Lumora is an up and coming tutoring business located on Sydney's Upper North Shore catering to school students of all ages. We need a flyer designed for notice boards and letter box drops to attract new clients. Our tutors are mostly university education students who are fresh, dedicated and passionate about their areas of teaching. The flyer should exhibit a bright, bold, modern, clean cut style which would appeal to both students and parents. I have attached our logo (the flyer could reflect this colour scheme), and a PDF which outlines the information we would like to appear on the flyer. This is not set in stone, but designed to act as an extremely loose guide for your creativity !

Target Market(s)

Affluent School Students and Parents

Industry/Entity Type

Tutoring

Requirements
Must have
• Logo, $10 offer, company description.
Nice to have
• Grabbing headlines to attract new clients, such as "Feeling overwhelmed at school?". We are looking for an eye catching, clean cut and professional design that has the colours to attract kids and the tone to attract parents.

```html
<!DOCTYPE html>
<html lang="en">
<head>
<meta charset="utf-8">
<title>Lumora Tutoring Flyer</title>
<link rel="stylesheet" href="https://fonts.googleapis.com/css2?family=Lato:wght@400;700&family=Roboto+Condensed:wght@400;700&display=swap">
<style>
  :root {
    --pink: #d3195e;
    --pink-bright: #e8437a;
    --crimson: #b3134a;
    --blue: #1f4f9e;
    --blue-dark: #173f85;
    --ring-blue: #2a5cb0;
    --ring-light: #a9c5ea;
    --ink: #3a3a3a;
    --paper: #ffffff;
    --panel: #e4e4e6;
    --shadow: rgba(0,0,0,0.18);
  }
  * { box-sizing: border-box; margin: 0; padding: 0; }
  html, body { width: 902px; height: 1200px; overflow: hidden; background: #f2f2f2; }
  .flyer {
    position: relative; width: 902px; height: 1200px; overflow: hidden;
    background: linear-gradient(180deg, #ffffff 0%, #f7f7f8 55%, #ececee 100%);
    font-family: "Lato", Arial, sans-serif; color: var(--ink);
  }
  .brand { position: absolute; left: 44px; top: 56px; width: 170px; text-align: center; }
  .brand-dot { width: 104px; height: 104px; border-radius: 50%; background: var(--pink-bright); margin: 0 auto 6px; }
  .brand-name { font-family: "Lato", Arial, sans-serif; font-weight: 400; font-size: 44px; color: #3c3c3c; line-height: 1; }

  .hero { position: absolute; left: 223px; top: 50px; width: 690px; height: 690px; }

  .offer {
    position: absolute; left: 58px; top: 250px; width: 376px; height: 376px; border-radius: 50%;
    background: radial-gradient(circle at 45% 38%, #d8336c 0%, var(--crimson) 70%, #9b0f3f 100%);
    border: 9px solid var(--paper); box-shadow: 0 4px 14px var(--shadow);
    display: flex; flex-direction: column; align-items: center; justify-content: center;
    text-align: center; color: #fff;
  }
  .offer-lead { font-size: 29px; line-height: 1.2; font-weight: 400; margin-top: 10px; }
  .offer-price { font-size: 84px; font-weight: 700; line-height: 1.05; }

  .intro { position: absolute; left: 34px; top: 728px; width: 386px; }
  .intro-title { font-family: "Roboto Condensed", Arial, sans-serif; font-weight: 700; font-size: 45px; line-height: 1; margin-bottom: 12px; }
  .intro-title .first { color: var(--pink); }
  .intro-title .second { color: var(--blue); }
  .intro p { font-size: 21px; line-height: 1.22; text-align: justify; margin-bottom: 10px; color: #3d3d3d; }

  .contact {
    position: absolute; left: 30px; top: 1000px; width: 384px; height: 170px;
    background: var(--paper); border-radius: 16px 16px 0 0; box-shadow: 0 0 10px var(--shadow);
    padding: 22px 16px 0 22px; font-family: "Roboto Condensed", Arial, sans-serif;
  }
  .contact li { list-style: none; display: flex; align-items: flex-start; gap: 12px; font-size: 19px; color: var(--pink); margin-bottom: 13px; line-height: 1.15; }
  .contact svg { flex: none; width: 16px; height: 16px; margin-top: 2px; fill: var(--blue-dark); }

  .panel { position: absolute; left: 433px; top: 752px; width: 469px; height: 414px; background: linear-gradient(90deg, #f4f4f5 0%, var(--panel) 60%, #d9d9db 100%); }
  .banner {
    position: absolute; left: 433px; width: 469px; padding-right: 38px; text-align: right; color: #fff;
    font-family: "Roboto Condensed", Arial, sans-serif; font-weight: 700;
  }
  .banner-hsc { top: 762px; height: 96px; font-size: 33px; line-height: 1.27; padding-top: 6px; background: linear-gradient(90deg, #f0f0f0 0%, var(--pink) 14%, var(--pink) 100%); }
  .banner-skills { top: 866px; height: 88px; font-size: 26px; line-height: 1.3; padding-top: 8px; background: linear-gradient(90deg, #f0f0f0 0%, var(--blue) 14%, var(--blue) 100%); }
  .banner-engage { top: 960px; height: 84px; font-size: 26px; line-height: 1.3; padding-top: 6px; background: linear-gradient(90deg, #f0f0f0 0%, var(--pink-bright) 14%, var(--pink-bright) 100%); }

  .cta { position: absolute; left: 470px; top: 1054px; width: 394px; text-align: right; }
  .cta-title { font-family: "Roboto Condensed", Arial, sans-serif; font-weight: 700; font-size: 33px; color: #fff; text-shadow: 1px 2px 3px rgba(0,0,0,0.45); }
  .cta-text { font-size: 19px; line-height: 1.3; color: #333; margin-top: 4px; }

  .footer-band { position: absolute; left: 0; top: 1166px; width: 902px; height: 34px; background: linear-gradient(90deg, #163a7c 0%, var(--blue) 55%, #2f64b8 75%, var(--blue-dark) 100%); }
</style>
</head>
<body>
<main class="flyer">
  <div class="brand">
    <div class="brand-dot"></div>
    <div class="brand-name">lumora</div>
  </div>

  <svg class="hero" viewBox="0 0 690 690" aria-hidden="false">
    <defs>
      <radialGradient id="heroFill" cx="0.55" cy="0.48" r="0.6">
        <stop offset="0" stop-color="#3a5fae"/>
        <stop offset="0.35" stop-color="#6f86b8"/>
        <stop offset="0.6" stop-color="#cfcac2"/>
        <stop offset="1" stop-color="#ebe8e2"/>
      </radialGradient>
    </defs>
    <circle cx="345" cy="345" r="340" fill="var(--ring-blue)"/>
    <circle cx="345" cy="345" r="330" fill="var(--ring-light)"/>
    <circle cx="345" cy="345" r="322" fill="#ffffff"/>
    <circle cx="345" cy="345" r="312" fill="url(#heroFill)" role="img" aria-label="Close-up photo of a keyboard with a blue Education key bearing a graduation cap"/>
  </svg>

  <div class="offer">
    <div class="offer-lead">Mention<br>this advertisement<br>to claim your trial<br>session for just</div>
    <div class="offer-price">$10!</div>
  </div>

  <section class="intro">
    <h1 class="intro-title"><span class="first">Lumora</span> <span class="second">Tutoring</span></h1>
    <p>offers one-on-one, individualised learning experiences to maximise academic development.</p>
    <p>Our tutors are hand selected on the basis of their qualifications, expertise and passion for inspiring young learners.</p>
  </section>

  <ul class="contact">
    <li><svg viewBox="0 0 16 16"><path d="M1 3h14v10H1z M2 4l6 5 6-5" fill="none" stroke="#173f85" stroke-width="1.6"/></svg>info@lumoratutoring.com.au</li>
    <li><svg viewBox="0 0 16 16"><circle cx="8" cy="8" r="7"/><path d="M1 8h14M8 1c-3 4-3 10 0 14M8 1c3 4 3 10 0 14" stroke="#fff" stroke-width="1" fill="none"/></svg>www.lumoratutoring.com.au</li>
    <li><svg viewBox="0 0 16 16"><path d="M8 1L0.5 8H3v7h4v-4h2v4h4V8h2.5z"/></svg>Suite 4, 220 Wattle Road Killara, NSW<br>2071</li>
  </ul>

  <div class="panel"></div>
  <div class="banner banner-hsc">Feeling overwhelmed by<br>the HSC?</div>
  <div class="banner banner-skills">Looking to improve your skills,<br>confidence and organisation?</div>
  <div class="banner banner-engage">Want to increase your child’s<br>engagement at school?</div>

  <div class="cta">
    <div class="cta-title">Contact us today</div>
    <div class="cta-text">to discuss how we can help make your<br>learning goals a reality!</div>
  </div>

  <div class="footer-band"></div>
</main>
</body>
</html>
```